Existing Website Requiring new Pages

I have an existing word press website that was built using elementor.
Website: www.tallowcrestcare.com.au
I require the Vacancies page (https://www.tallowcrestcare.com.au/vacancies/) to be modified to display our new properties along with minor tweaks to how the information is presented.
The vacancies to be displayed are the exactly the same as those that are located on the homepage of QMR website (https://qmr.org.au/)
The new pages that link off the Vacancies tab will require custom design.
There are roughly 8 pages/properties to be incorporated. i wish for the design to be very similar to that displayed in the following link; https://www.polunda.com.au/vacancies/merrylands
Along with this the back end has not been updated for the last 3 years so it also requires some maintenance.
Website is in the disability industry and the custom pages will display information relative to Property Vacancies.
I have attached a ZIP file with some design guides, the information for each of the properties (which will need to be modified to show our business name Tallowcrest Care) and the example of how it is to look based off the Polunda website.
If you guys have any suggestions or ideas on how to make this more presentable or possible i'm open to your ideas.
Target Market(s)
People looking for SDA properties custom built for people with a disability
Industry/Entity Type
Disability
Coding
Coded - Design and coding required
Number of Pages Required
5+ page

```html
<!DOCTYPE html>
<html lang="en">
<head>
<meta charset="utf-8">
<title>Vacancies – Tallowcrest Care</title>
<link rel="stylesheet" href="https://fonts.googleapis.com/css2?family=Varela+Round&family=Mulish:wght@400;600;700;800&display=swap">
<style>
:root{
  --ink:#2b2b2b;
  --nav:#3a3a3a;
  --accent-orange:#f0923a;
  --hero-orange:#f4b25c;
  --purple:#775fc4;
  --pink:#e6479a;
  --muted:#8a8a8a;
  --rule:#e6e6e6;
  --blue:#1b8fd6;
  --dark:#1f1f1f;
  --white:#ffffff;
}
*{box-sizing:border-box;margin:0;padding:0}
html,body{width:1200px;height:2460px;overflow:hidden;background:var(--white)}
body{position:relative;font-family:"Mulish",sans-serif;color:var(--ink)}
.abs{position:absolute}

/* header */
.site-header{position:absolute;left:0;top:0;width:1200px;height:144px;background:var(--white)}
.brand{position:absolute;left:113px;top:40px;display:flex;align-items:center;gap:8px}
.brand-dot{width:22px;height:22px;border-radius:50%;background:var(--pink)}
.brand-name{font-family:"Varela Round",sans-serif;font-size:22px;color:var(--purple)}
.main-nav{position:absolute;top:55px;left:567px;display:flex;gap:0;font-size:11px;font-weight:800;letter-spacing:.6px;text-transform:uppercase;color:var(--nav)}
.main-nav span{margin-right:24px}
.main-nav .current{color:var(--accent-orange)}
.main-nav .last{margin-right:0}

/* hero */
.hero{position:absolute;left:0;top:144px;width:1200px;height:453px;overflow:hidden;
  background:linear-gradient(100deg,#c98a45 0%,#8a7a6c 45%,#6c6460 70%,#4c4240 100%)}
.hero-tint{position:absolute;inset:0}
.hero-title{position:absolute;left:113px;top:200px;font-family:"Varela Round",sans-serif;font-size:46px;color:var(--white);letter-spacing:1px;text-shadow:0 2px 6px rgba(0,0,0,.25)}

/* listing */
.section-title{position:absolute;left:0;top:684px;width:1200px;text-align:center;font-family:"Varela Round",sans-serif;font-size:32px;letter-spacing:1.5px;color:var(--ink)}
.feature-photo{position:absolute;left:113px;top:778px;width:487px;height:592px;
  background:linear-gradient(180deg,#e8ecef 0%,#c9cfd4 35%,#7d766f 55%,#5f6f4e 70%,#a9a7a2 85%,#c4c2bd 100%);
  box-shadow:0 10px 30px rgba(0,0,0,.12)}
.feature-card{position:absolute;left:475px;top:843px;width:612px;height:462px;background:var(--purple);color:var(--white);padding:52px 55px 0 53px}
.feature-card h2{font-family:"Varela Round",sans-serif;font-weight:400;font-size:31px;letter-spacing:1px;margin-bottom:14px}
.feature-card p{font-size:17px;line-height:30px;letter-spacing:.3px;padding-left:2px}
.feature-card h3{font-family:"Varela Round",sans-serif;font-weight:400;font-size:24px;letter-spacing:.8px;margin:18px 0 20px 2px;-webkit-text-stroke:.5px var(--white)}
.btn{display:inline-block;margin-left:2px;width:149px;height:44px;line-height:44px;text-align:center;background:var(--pink);font-size:13px;font-weight:800;letter-spacing:1px;border-radius:2px}

.property-grid{position:absolute;left:113px;top:1446px;width:974px;display:grid;grid-template-columns:repeat(4,234px);column-gap:13px;row-gap:0}
.property{height:314px}
.thumb{width:234px;height:235px;border-radius:8px}
.thumb.active{border:3px solid var(--purple)}
.property-name{margin-top:18px;text-align:center;font-family:"Varela Round",sans-serif;font-size:22px;letter-spacing:1px;color:var(--ink)}
.t1{background:linear-gradient(180deg,#e9edf1 0%,#b9bec4 40%,#6f6a64 58%,#557040 75%,#8d8a86 100%)}
.t2{background:linear-gradient(180deg,#cfe2f2 0%,#a9564a 30%,#6d8a3f 55%,#c98a6c 80%,#c27d62 100%)}
.t3{background:linear-gradient(180deg,#3f8fd6 0%,#89b4dc 30%,#e4dcc2 55%,#6f9a44 80%,#7da84e 100%)}
.t4{background:linear-gradient(180deg,#6fa3d6 0%,#cfc3aa 40%,#b9ab90 65%,#7da64c 90%,#6f9c42 100%)}
.t5{background:linear-gradient(180deg,#9cc3e6 0%,#c7c9c4 35%,#b98e6c 55%,#4f8a3a 78%,#63a542 100%)}
.t6{background:linear-gradient(180deg,#5ea0de 0%,#b9d2e8 30%,#b9674a 55%,#6f9c48 75%,#c9c6bf 100%)}
.t7{background:linear-gradient(180deg,#6f9bc9 0%,#f0c98a 35%,#9a8c7f 55%,#5d5d5c 80%,#3f4a3a 100%)}
.t8{background:linear-gradient(180deg,#8fb3d6 0%,#9fae92 30%,#e3e0d6 55%,#c9874f 80%,#7a6f62 100%)}

/* footer */
.site-footer{position:absolute;left:0;top:2128px;width:1200px;height:272px;background:var(--white);box-shadow:0 -8px 16px rgba(0,0,0,.04)}
.footer-brand{position:absolute;left:140px;top:92px;display:flex;align-items:center;gap:8px}
.footer-contact{position:absolute;left:137px;top:188px;font-size:12px;color:var(--muted);line-height:21px}
.footer-contact li{list-style:none;display:flex;align-items:center;gap:7px}
.footer-contact svg{width:13px;height:13px}
.social{position:absolute;left:525px;top:52px;display:flex;flex-direction:column;gap:8px}
.social span{width:30px;height:30px;border-radius:50%;display:block}
.s1{background:#5a2a82}.s2{background:#1a5fb4}.s3{background:#111}.s4{background:#1b7bc4}
.footer-col{position:absolute;top:42px;width:216px}
.footer-col h4{font-size:13px;font-weight:600;letter-spacing:.5px;color:var(--ink);border-left:2px solid var(--blue);padding-left:12px;line-height:14px;padding-bottom:12px;border-bottom:1px solid var(--rule);border-left-width:2px}
.footer-col li{list-style:none;font-size:12px;color:var(--muted);line-height:21px;padding:6px 0 4px;border-bottom:1px solid var(--rule);letter-spacing:.2px}
.col-acc{left:612px}
.col-what{left:850px}

.bottom-bar{position:absolute;left:0;top:2400px;width:1200px;height:60px;background:var(--dark);color:#bdbdbd;font-size:10px}
.bottom-bar .copy{position:absolute;left:0;width:1200px;top:25px;text-align:center}
.bottom-bar .code{position:absolute;right:56px;top:25px;color:var(--white)}
.to-top{position:absolute;right:0;top:14px;width:38px;height:34px;background:#111}
</style>
</head>
<body>

<header class="site-header">
  <div class="brand"><span class="brand-dot"></span><span class="brand-name">Tallowcrest Care</span></div>
  <nav class="main-nav">
    <span>Home</span><span>About Us</span><span class="current">What We Do ⌄</span><span>Referrals</span><span>Feedback</span><span class="last">Contact Us</span>
  </nav>
</header>

<section class="hero">
  <div class="hero-tint" role="img" aria-label="Office scene of a smiling woman using a wheelchair at a desk with colleagues behind, left part washed in warm orange"></div>
  <svg class="abs" style="left:0;top:0" width="1200" height="453" aria-hidden="true">
    <polygon points="0,0 430,0 608,453 0,453" fill="#f4b25c" opacity=".88"/>
  </svg>
  <h1 class="hero-title">Vacancies</h1>
</section>

<h2 class="section-title">4 BEDROOM SIL HOME</h2>

<div class="feature-photo" role="img" aria-label="Photo of the Penrith single-storey brick home with garage and paved driveway"></div>
<article class="feature-card">
  <h2>PENRITH</h2>
  <p>Sed ut perspiciatis unde omnis iste natus error sit voluptatem accusantium doloremque laudantium, totam rem aperiam, eaque ipsa quae ab illo inventore veritatis et quasi architecto beatae vitae dicta sunt explicabo. Nemo enim ipsam voluptatem quia voluptas sit aspernatur aut odit aut fugit, sed quia consequuntur</p>
  <h3>4 Bedroom SIL Home</h3>
  <span class="btn">VIEW DETAILS</span>
</article>

<div class="property-grid">
  <div class="property"><div class="thumb t1 active" role="img" aria-label="Penrith home photo"></div><div class="property-name">Penrith</div></div>
  <div class="property"><div class="thumb t2" role="img" aria-label="Mount Druitt home photo"></div><div class="property-name">Mount Druitt</div></div>
  <div class="property"><div class="thumb t3" role="img" aria-label="Casula home photo"></div><div class="property-name">Casula</div></div>
  <div class="property"><div class="thumb t4" role="img" aria-label="Eastwood home photo"></div><div class="property-name">Eastwood</div></div>
  <div class="property"><div class="thumb t5" role="img" aria-label="Baulkham Hills home photo"></div><div class="property-name">Baulkham Hills</div></div>
  <div class="property"><div class="thumb t6" role="img" aria-label="Merrylands home photo"></div><div class="property-name">Merrylands</div></div>
  <div class="property"><div class="thumb t7" role="img" aria-label="Alcatraz Island city view at sunset"></div><div class="property-name">Alcatraz Island</div></div>
  <div class="property"><div class="thumb t8" role="img" aria-label="Golden Gate Park hillside houses"></div><div class="property-name">Golden Gate Park</div></div>
</div>

<footer class="site-footer">
  <div class="footer-brand"><span class="brand-dot"></span><span class="brand-name">Tallowcrest Care</span></div>
  <ul class="footer-contact">
    <li><svg viewBox="0 0 14 14"><rect x="1" y="3" width="12" height="8" fill="none" stroke="#e6479a" stroke-width="1.3"/><path d="M1 3l6 5 6-5" fill="none" stroke="#e6479a" stroke-width="1.3"/></svg>Email: info@tallowcrestcare.com.au</li>
    <li><svg viewBox="0 0 14 14"><path d="M3 1l3 3-2 2c1 2 2 3 4 4l2-2 3 3-2 2C6 13 1 8 1 3z" fill="#e6479a"/></svg>Phone: +61 0400 318 562</li>
    <li><svg viewBox="0 0 14 14"><circle cx="7" cy="7" r="5.5" fill="none" stroke="#e6479a" stroke-width="1.3"/><path d="M7 4v3.5l2 1.5" fill="none" stroke="#e6479a" stroke-width="1.3"/></svg>Operating Hours: 9AM To 5PM Monday - Friday</li>
  </ul>
  <div class="social"><span class="s1"></span><span class="s2"></span><span class="s3"></span><span class="s4"></span></div>
  <div class="footer-col col-acc">
    <h4>ACCOMMODATION</h4>
    <ul>
      <li>Supported Independent Living (SIL)</li>
      <li>Specialist Disability Accommodation (SDA)</li>
      <li>Short term Accommodation (Respite)</li>
      <li>Vacancies</li>
    </ul>
  </div>
  <div class="footer-col col-what">
    <h4>WHAT WE DO</h4>
    <ul>
      <li>In Home Care</li>
      <li>Social &amp; Community Services</li>
      <li>Therapeutic Supports</li>
      <li>Support Coordination</li>
      <li>Home Modifications</li>
    </ul>
  </div>
</footer>

<div class="bottom-bar">
  <div class="copy">© Copyright 2021 | Tallowcrest Care | All Rights Reserved.</div>
  <div class="code">C58</div>
  <div class="to-top"><svg width="38" height="34" aria-hidden="true"><path d="M15 20l4-5 4 5z" fill="#fff"/></svg></div>
</div>

</body>
</html>
```